Corvane Freight Company Business Card Design

We are a company that delivers natural saltwater (from the ocean) to aquarium companies, restaurants and home marine tanks. I would like a new business card to suit.

Must include Name, company name, abn, contact number and website as well as logo (see attached).

Looking for a design that stands out, has a clean but unique appearance.

Double and single sided entries welcome

Business

• Logo

```html
<!DOCTYPE html>
<html lang="en">
<head>
<meta charset="utf-8">
<title>Corvane Freight Company – Business Cards</title>
<link rel="stylesheet" href="https://fonts.googleapis.com/css2?family=Source+Sans+3:wght@400;600;700&display=swap">
<style>
  :root {
    --stage: #1c1c1c;
    --paper: #ffffff;
    --ocean-deep: #055aa8;
    --ocean-light: #55c9f2;
    --brand-blue: #0b8fd0;
    --ink-deep: #0a4f94;
  }
  * { box-sizing: border-box; margin: 0; padding: 0; }
  html, body { width: 1200px; height: 750px; overflow: hidden; background: var(--stage); }
  body { position: relative; font-family: "Source Sans 3", "Myriad Pro", Arial, sans-serif; }

  .card {
    position: absolute;
    width: 516px;
    height: 294px;
    overflow: hidden;
    background: var(--paper);
  }
  .card--front-light { left: 72px; top: 63px; }
  .card--front-deep  { left: 606px; top: 63px; }
  .card--back { left: 342px; top: 400px; background: var(--ocean-deep); }

  .brand {
    position: absolute;
    left: 0; right: 0; top: 0; height: 180px;
    display: flex; align-items: center; justify-content: center; gap: 10px;
  }
  .brand__dot {
    width: 16px; height: 16px; border-radius: 50%;
    background: var(--brand-blue);
    flex: none;
  }
  .brand__name {
    color: var(--brand-blue);
    font-weight: 600;
    font-size: 34px;
    letter-spacing: -0.3px;
    white-space: nowrap;
  }

  .name-band {
    position: absolute; left: 0; right: 0; top: 180px; height: 29px;
    display: flex; align-items: center; justify-content: center;
    color: #fff; font-size: 16px;
  }
  .name-band strong { font-weight: 700; font-size: 18px; margin-right: 5px; }
  .rule { position: absolute; left: 0; right: 0; top: 209px; height: 3px; background: var(--paper); }
  .contact {
    position: absolute; left: 0; right: 0; top: 212px; bottom: 0;
    text-align: center; font-size: 13px; line-height: 17px;
    padding-top: 12px;
  }
  .contact__line { display: flex; justify-content: center; gap: 18px; margin-bottom: 13px; }
  .contact__item { display: inline-flex; align-items: center; gap: 6px; }
  .contact__item svg { width: 10px; height: 10px; }

  .card--front-light .name-band { background: var(--ocean-deep); }
  .card--front-light .contact { background: var(--ocean-light); color: var(--ink-deep); }
  .card--front-light svg { stroke: var(--ink-deep); fill: none; }

  .card--front-deep .name-band { background: var(--ocean-light); }
  .card--front-deep .contact { background: var(--ocean-deep); color: #fff; }
  .card--front-deep svg { stroke: #fff; fill: none; }

  .back-oval {
    position: absolute; left: 40px; top: 56px; width: 436px; height: 188px;
    border-radius: 50%; background: var(--paper);
    display: flex; align-items: center; justify-content: center; gap: 10px;
  }
</style>
</head>
<body>

  <section class="card card--front-light">
    <div class="brand"><span class="brand__dot"></span><span class="brand__name">Corvane Freight Company</span></div>
    <div class="name-band"><strong>Your Name,</strong> Title</div>
    <div class="rule"></div>
    <div class="contact">
      <div class="contact__line">
        <span class="contact__item"><svg viewBox="0 0 10 10" stroke-width="1.3"><path d="M2 1 L4 3 L3 4.5 Q4.5 6.5 5.5 7 L7 6 L9 8 L7.5 9.3 Q3 8.5 0.8 2.5 Z"/></svg>123-456-7892</span>
        <span class="contact__item"><svg viewBox="0 0 10 10" stroke-width="1"><circle cx="5" cy="5" r="4.3"/><ellipse cx="5" cy="5" rx="2" ry="4.3"/><path d="M0.7 5 H9.3"/></svg>www.corvanefreight.com</span>
      </div>
      <div>Street Name, City Name, State, Zip Code</div>
      <div>ABN: 123456789</div>
    </div>
  </section>

  <section class="card card--front-deep">
    <div class="brand"><span class="brand__dot"></span><span class="brand__name">Corvane Freight Company</span></div>
    <div class="name-band"><strong>Your Name,</strong> Title</div>
    <div class="rule"></div>
    <div class="contact">
      <div class="contact__line">
        <span class="contact__item"><svg viewBox="0 0 10 10" stroke-width="1.3"><path d="M2 1 L4 3 L3 4.5 Q4.5 6.5 5.5 7 L7 6 L9 8 L7.5 9.3 Q3 8.5 0.8 2.5 Z"/></svg>123-456-7892</span>
        <span class="contact__item"><svg viewBox="0 0 10 10" stroke-width="1"><circle cx="5" cy="5" r="4.3"/><ellipse cx="5" cy="5" rx="2" ry="4.3"/><path d="M0.7 5 H9.3"/></svg>www.corvanefreight.com</span>
      </div>
      <div>Street Name, City Name, State, Zip Code</div>
      <div>ABN: 123456789</div>
    </div>
  </section>

  <section class="card card--back">
    <div class="back-oval"><span class="brand__dot"></span><span class="brand__name">Corvane Freight Company</span></div>
  </section>

</body>
</html>
```